QVR business card

Need a business card for a company that provides instructional design and elearning development services. The website is here: http://quorvane.studio/

I'm attaching a current logo, as well as the old business card design. While I like to keep it clean, the old design is too simplistic for my liking. The only idea I want to reuse from the old design is placing industry jargon on the back of the card, just need a better way to present it. But if you have other ideas for the back--feel free to experiment.

Please use the colors complementary to the color we have on the website. Thank you!

```html
<!DOCTYPE html>
<html lang="en">
<head>
<meta charset="utf-8">
<title>QVR Business Card</title>
<link rel="stylesheet" href="https://fonts.googleapis.com/css2?family=Open+Sans:wght@400;600;700&display=swap">
<style>
  :root {
    --teal: #16b2ae;
    --teal-soft: #5cc0b4;
    --sand: #dccb8f;
    --gold: #e2c777;
    --stripe: #d9c98e;
    --white: #ffffff;
    --ink: #2b2b2b;
    --backdrop: #ecebe8;
  }
  * { box-sizing: border-box; margin: 0; padding: 0; }
  html, body { width: 1200px; height: 675px; overflow: hidden; }
  body {
    background: var(--backdrop);
    font-family: "Open Sans", Arial, sans-serif;
    position: relative;
  }
  .card {
    position: absolute;
    top: 189px;
    width: 520px;
    height: 297px;
    overflow: hidden;
    box-shadow: 0 6px 18px rgba(0,0,0,0.18);
  }

  /* Back of card */
  .card-back {
    left: 45px;
    background: linear-gradient(170deg, var(--teal) 0%, var(--teal-soft) 45%, var(--sand) 100%);
  }
  .world-map {
    position: absolute;
    left: 120px; top: 70px;
    width: 310px; height: 170px;
    border-radius: 40px;
    background: radial-gradient(ellipse at center, rgba(255,255,255,0.22), rgba(255,255,255,0) 70%);
  }
  .mark-placeholder {
    position: absolute;
    left: 244px; top: 30px;
    width: 34px; height: 34px;
    border-radius: 50%;
    background: var(--white);
  }
  .services {
    position: absolute;
    left: 0; right: 0; top: 86px;
    display: flex; flex-direction: column; align-items: center; gap: 5px;
  }
  .service-tag {
    background: var(--teal);
    color: var(--white);
    font-size: 15px;
    line-height: 1;
    padding: 4px 10px;
    border-radius: 3px;
  }
  .back-web {
    position: absolute;
    left: 0; right: 0; top: 214px;
    text-align: center;
    color: var(--white);
    font-size: 12px;
  }

  /* Front of card */
  .card-front {
    left: 635px;
    background: var(--white);
  }
  .front-panel { position: absolute; inset: 0; }
  .person {
    position: absolute;
    left: 22px; top: 20px;
  }
  .person-name {
    color: var(--gold);
    font-weight: 700;
    font-size: 15px;
    letter-spacing: 0.5px;
  }
  .person-role {
    color: var(--white);
    font-size: 12px;
    margin-top: 1px;
  }
  .contacts {
    position: absolute;
    left: 22px; bottom: 36px;
    list-style: none;
    color: var(--white);
    font-size: 13px;
  }
  .contacts li { display: flex; align-items: center; gap: 7px; line-height: 20px; }
  .contacts svg { width: 12px; height: 12px; flex: none; }
  .brand {
    position: absolute;
    left: 352px; top: 108px;
    display: flex; align-items: center; gap: 9px;
  }
  .brand-dot {
    width: 18px; height: 18px;
    border-radius: 50%;
    background: var(--teal);
  }
  .brand-name {
    color: var(--teal);
    font-weight: 700;
    font-size: 34px;
    letter-spacing: 1px;
  }
</style>
</head>
<body>

<section class="card card-back" aria-label="Business card back">
  <div class="world-map" role="img" aria-label="Dotted world map background"></div>
  <div class="mark-placeholder"></div>
  <div class="services">
    <span class="service-tag">Instructional Design</span>
    <span class="service-tag">Elearning Development | Mobile Learning</span>
    <span class="service-tag">Insructor-LED Training</span>
  </div>
  <p class="back-web">www.quorvane.studio</p>
</section>

<section class="card card-front" aria-label="Business card front">
  <svg class="front-panel" viewBox="0 0 520 297" preserveAspectRatio="none" aria-hidden="true">
    <polygon points="0,0 336,0 298,297 0,297" fill="var(--teal)"/>
    <polygon points="340,0 346,0 308,297 302,297" fill="var(--stripe)"/>
  </svg>

  <div class="person">
    <p class="person-name">Marten Ovidal</p>
    <p class="person-role">Managing Director</p>
  </div>

  <ul class="contacts">
    <li>
      <svg viewBox="0 0 12 12" aria-hidden="true"><path d="M2 1h2l1 3-1.3 1a6 6 0 0 0 3.3 3.3L8 7l3 1v2a1 1 0 0 1-1 1A9 9 0 0 1 1 2a1 1 0 0 1 1-1z" fill="var(--gold)"/></svg>
      555-013-2748
    </li>
    <li>
      <svg viewBox="0 0 12 12" aria-hidden="true"><rect x="0.5" y="2" width="11" height="8" rx="1" fill="var(--gold)"/><path d="M1 2.5l5 4 5-4" stroke="var(--teal)" stroke-width="1" fill="none"/></svg>
      movidal@quorvane.studio
    </li>
    <li>
      <svg viewBox="0 0 12 12" aria-hidden="true"><circle cx="6" cy="6" r="5.3" fill="var(--gold)"/><path d="M0.8 6h10.4M6 0.8c-2.6 2.8-2.6 7.6 0 10.4M6 0.8c2.6 2.8 2.6 7.6 0 10.4" stroke="var(--teal)" stroke-width="0.8" fill="none"/></svg>
      www.quorvane.studio
    </li>
  </ul>

  <div class="brand">
    <span class="brand-dot"></span>
    <span class="brand-name">QVR</span>
  </div>
</section>

</body>
</html>
```